Copper Lantern Gin

The gin is 100% proof and men and anbody 18 - 30 year old will be a target market - the bottle is very distinctive and lends itself to a square label.

The bottle is curved with a large front face that lends itself to a striking design. There should be enough space around the label to show the black gin in the bottle as this is a feature.

The current bottle with the existing label is attached below as is the new glass bottle. The new gin will be coloured black.

Font styles to use
Decorative
Script

```html
<!DOCTYPE html>
<html lang="en">
<head>
<meta charset="utf-8">
<title>Copper Lantern Gin – Label</title>
<link rel="stylesheet" href="https://fonts.googleapis.com/css2?family=Bodoni+Moda:wght@400;500&family=Pinyon+Script&display=swap">
<style>
  :root {
    --paper: #ffffff;
    --label-black: #000000;
    --silver-light: #ffffff;
    --silver-mid: #c9c9c9;
    --silver-dark: #6f6f6f;
    --crimson: #8a0d22;
    --crimson-deep: #5a0614;
  }
  html, body {
    margin: 0;
    padding: 0;
    width: 1200px;
    height: 1000px;
    overflow: hidden;
    background: var(--paper);
  }
  .gin-label {
    display: block;
    width: 1200px;
    height: 1000px;
  }
  .label-field { fill: var(--label-black); }
  .label-frame { fill: none; stroke: url(#silver-sheen); stroke-width: 18; }
  .strength-line,
  .gin-letter,
  .bottle-detail {
    font-family: "Bodoni Moda", "Didot", serif;
    fill: url(#silver-sheen);
  }
  .strength-line { font-size: 172px; font-weight: 400; }
  .gin-letter { font-size: 582px; font-weight: 400; }
  .bottle-detail { font-size: 92px; font-weight: 400; }
  .bottle-detail .unit { font-size: 34px; }
  .brand-name {
    font-family: "Pinyon Script", cursive;
    font-size: 140px;
    fill: url(#crimson-sheen);
  }
</style>
</head>
<body>
<svg class="gin-label" viewBox="0 0 1200 1000" xmlns="http://www.w3.org/2000/svg">
  <defs>
    <linearGradient id="silver-sheen" x1="0" y1="0" x2="1200" y2="1000" gradientUnits="userSpaceOnUse" spreadMethod="reflect">
      <stop offset="0" style="stop-color: var(--silver-light)"/>
      <stop offset="0.12" style="stop-color: var(--silver-dark)"/>
      <stop offset="0.22" style="stop-color: var(--silver-light)"/>
      <stop offset="0.35" style="stop-color: var(--silver-mid)"/>
      <stop offset="0.45" style="stop-color: var(--silver-light)"/>
      <stop offset="0.55" style="stop-color: var(--silver-dark)"/>
      <stop offset="0.68" style="stop-color: var(--silver-light)"/>
      <stop offset="0.82" style="stop-color: var(--silver-mid)"/>
      <stop offset="1" style="stop-color: var(--silver-light)"/>
    </linearGradient>
    <linearGradient id="crimson-sheen" x1="0" y1="688" x2="0" y2="830" gradientUnits="userSpaceOnUse">
      <stop offset="0" style="stop-color: var(--crimson-deep)"/>
      <stop offset="1" style="stop-color: var(--crimson)"/>
    </linearGradient>
  </defs>

  <rect class="label-field" x="19" y="18" width="1162" height="964"/>
  <rect class="label-frame" x="19" y="18" width="1162" height="964"/>

  <text class="strength-line" x="184" y="178" textLength="832" lengthAdjust="spacingAndGlyphs">NAVY STRENGTH BRITISH</text>

  <text class="gin-letter" x="184" y="654" textLength="102" lengthAdjust="spacingAndGlyphs">G</text>
  <text class="gin-letter" x="548" y="654" textLength="66" lengthAdjust="spacingAndGlyphs">I</text>
  <text class="gin-letter" x="876" y="654" textLength="140" lengthAdjust="spacingAndGlyphs">N</text>

  <text class="brand-name" x="56" y="812" textLength="1088" lengthAdjust="spacingAndGlyphs">Copper Lantern</text>

  <text class="bottle-detail" x="266" y="942" textLength="70" lengthAdjust="spacingAndGlyphs">50<tspan class="unit">CL</tspan></text>
  <text class="bottle-detail" x="804" y="942" textLength="132" lengthAdjust="spacingAndGlyphs">57%<tspan class="unit">ABV</tspan></text>
</svg>
</body>
</html>
```